Home Page Design (+50 More Pages To Winning Designer!)

We have a 50+ page website, but we're starting with the home page. The winning designer will get all 50+ pages to design as a 2nd project, so make sure you do your best!

Velorane is in the private jet industry and needs a re-designed website.

We have created the structure for the website and content inside of Frandle.io (THESE ARE ONLY ROUGH A.I. GENERATED WIREFRAMES AND DO NOT NEED TO BE FOLLOWED EXACTLY) - https://www.frandle.io/app/project/K482915_qWmRtZaLs-KDnHoUvvy82QJ5cfhaR61trkwqlDV3Hm

Take the content from the 'Home Page' under the 'Wireframe' tab on the Frandle.io link above, but feel free to re-design the page in a better way as these are only A.I. generated wireframes.

We want a DARK theme.... High quality, luxurious feel, greyscale colors. Attached is a brand guideline (BUT THIS IS NOT A 100% BRAND GUIDELINE, YOU CAN CHANGE COLORS AND FONTS AND MAKE CHANGES IF YOU HAVE BETTER IDEAS) and attached is our logo. We are also attaching some examples of other apps and websites to give you a guideline of what we're looking for for this design project.

The final design MUST communicate luxury using high-quality imagery of large cabin luxurious private jets.
Updates

ENTRIES THAT DO NOT FOLLOW THE PROJECT BRIEF WILL BE AUTOMATICALLY DISCARDED. FOLLOW THE INSTRUCTIONS!

Industry/Entity Type

Travel

Number of Pages Required

1 page

Font styles to use
Sans Serif

Colors

Designer to choose colors to be used in the design.

Requirements
Must have
• Follow wireframe and use content in wireframe (see Frandle.io link)

```html
<!DOCTYPE html>
<html lang="en">
<head>
<meta charset="utf-8">
<title>Velorane — Private Jets</title>
<link href="https://fonts.googleapis.com/css2?family=Outfit:wght@300;400;500&family=Inter:wght@400;500;600&display=swap" rel="stylesheet">
<style>
:root{
  --bg:#0c0b15;
  --bg-deep:#07070c;
  --panel:#26252c;
  --ink:#ffffff;
  --muted:#b9b8c4;
  --dim:#7b7a88;
  --accent:#2d9ec9;
  --blue:#3f5fd1;
  --purple:#3c1a68;
  --purple-btn:#5a3596;
  --card:#f4f4f6;
}
*{box-sizing:border-box;margin:0;padding:0}
html,body{width:1200px;height:4918px;overflow:hidden;background:#fff}
body{font-family:"Inter",sans-serif;color:var(--ink)}
.page{position:relative;width:1200px;height:4803px;overflow:hidden;
  background:
   radial-gradient(600px 500px at 1000px 1900px,rgba(80,60,140,.25),transparent 70%),
   radial-gradient(700px 600px at 100px 400px,rgba(60,50,120,.28),transparent 70%),
   linear-gradient(180deg,#100d1e 0,#0a0a14 1400px,#0d0c1a 2400px,var(--bg) 2800px);}
.abs{position:absolute}
.h-font{font-family:"Outfit",sans-serif;font-weight:400}
/* nav */
.brand{display:flex;align-items:center;gap:8px;font-family:"Outfit",sans-serif;font-size:28px;font-weight:300;color:var(--ink)}
.brand-mark{width:20px;height:20px;background:var(--ink);border-radius:3px}
.nav{left:116px;top:20px;width:968px;height:40px;display:flex;align-items:center;justify-content:space-between}
.nav ul{display:flex;gap:32px;list-style:none;font-size:16px;margin-left:auto;margin-right:40px}
.login{background:#55545c;border-radius:10px;padding:10px 28px;font-size:16px}
/* hero */
.hero-photo{left:387px;top:143px;width:813px;height:544px;background:linear-gradient(180deg,#6e6a74 0,#8a7d7a 35%,#3f3c44 70%,#1b1a20 100%)}
.hero-card{left:118px;top:176px;width:443px;height:417px;background:rgba(120,118,130,.55);backdrop-filter:blur(8px);border:1px solid rgba(255,255,255,.15);padding:40px 28px}
.hero-card h1{font-family:"Outfit",sans-serif;font-weight:400;font-size:38px;line-height:57px;color:#1b1b22}
.hero-card h1 em{font-style:normal;color:var(--blue)}
.hero-card p{margin-top:24px;font-size:16px;line-height:26px;color:#3a3945}
.search{left:118px;top:690px;width:836px;height:104px;background:rgba(120,118,130,.6);display:flex;align-items:center;gap:22px;padding:0 20px}
.field{width:198px;height:64px;background:#fff;display:flex;align-items:center;gap:14px;padding:0 18px;color:#222}
.field small{display:block;font-size:10px;color:#888}
.field span{font-size:14px}
.explore{width:136px;height:64px;background:var(--blue);display:flex;align-items:center;justify-content:center;font-size:15px}
/* destinations */
.section-title{font-family:"Outfit",sans-serif;font-weight:400;font-size:40px}
.arrow-btn{width:40px;height:40px;border-radius:50%;background:#9c9ba6;display:flex;align-items:center;justify-content:center}
.dest{top:977px;width:332px;height:399px;background:var(--card);border-radius:16px;padding:14px;color:#222}
.dest .photo{height:250px;border-radius:8px}
.dest h3{margin-top:20px;font-size:15px;font-weight:600}
.dest p{font-size:10px;color:#999;line-height:13px;margin-top:6px}
.dest .meta{position:absolute;left:14px;right:14px;bottom:12px;display:flex;justify-content:space-between;font-size:14px}
/* about */
.lead{font-size:20px;line-height:31px}
.point h4{font-family:"Outfit",sans-serif;font-weight:400;font-size:28px;color:var(--accent);line-height:42px}
.point p{margin-top:16px;font-size:14px;line-height:23px;width:250px}
.engine{left:708px;top:1734px;width:368px;height:485px;background:linear-gradient(160deg,#8b8c90,#5c5d62 55%,#3b3c40)}
/* why */
.why-card{top:2463px;width:214px;height:237px;background:var(--panel);border-radius:6px;padding:18px 16px}
.why-card b{font-family:"Outfit",sans-serif;font-size:24px;color:var(--blue)}
.why-card h4{font-weight:400;font-size:16px;color:var(--blue);margin-top:6px}
.why-card p{font-size:13px;line-height:21px;margin-top:16px}
/* locations */
.loc-band{left:0;top:2824px;width:1200px;height:135px;background:var(--bg-deep)}
.map{left:0;top:2959px;width:1200px;height:378px;background:linear-gradient(120deg,#1d2a5a,#243668 50%,#1f2e5c)}
/* testimonials */
.testi{left:0;top:3337px;width:1200px;height:489px;background:#171a2a}
.quote{background:#fff;color:#222;padding:22px 28px}
.back{left:641px;top:3539px;width:420px;height:195px;background:#b8b7bd;padding:0 28px;color:#555}
.avatar{left:570px;top:3438px;width:56px;height:56px;border-radius:50%;background:#d9b35a}
/* contact */
.contact{left:113px;top:3898px;width:975px;height:347px;background:var(--purple);border-radius:8px}
.mail{left:317px;top:4091px;width:563px;height:57px;background:#fff;border-radius:8px;display:flex;align-items:center;padding:0 8px 0 20px;color:#999;font-size:13px}
.send{margin-left:auto;background:var(--purple-btn);color:#fff;border-radius:6px;padding:12px 36px;font-size:13px}
/* footer */
.foot{font-size:14px;line-height:20px}
.foot h5{font-size:14px;font-weight:600;margin-bottom:14px}
.foot li{list-style:none;margin-bottom:15px;font-size:14px}
.social{width:32px;height:32px;border-radius:50%;background:#fff}
</style>
</head>
<body>
<div class="page">
  <nav class="abs nav">
    <div class="brand">Velorane<span class="brand-mark"></span></div>
    <ul><li>Home</li><li>About</li><li>Why Us</li><li>Location</li><li>Review</li><li>Contact</li></ul>
    <div class="login">Login</div>
  </nav>

  <div class="abs hero-photo" role="img" aria-label="Private jet on a runway at dusk under a cloudy sky"></div>
  <div class="abs hero-card">
    <h1>Flying in <em>Style.</em><br>Discover Your<br>Freedom with <em>Private Jets</em></h1>
    <p>From personalized service to unmatched comfort, we're ready to take you to your dream destinations with unforgettable luxury.</p>
  </div>
  <div class="abs search">
    <div class="field"><svg width="20" height="20" viewBox="0 0 24 24" fill="none" stroke="#333" stroke-width="2"><path d="M12 22s7-7 7-12a7 7 0 0 0-14 0c0 5 7 12 7 12z"/><circle cx="12" cy="10" r="2.5"/></svg><div><small>Location</small><span>Paris</span></div><span style="margin-left:auto">⌄</span></div>
    <div class="field"><svg width="20" height="20" viewBox="0 0 24 24" fill="none" stroke="#333" stroke-width="2"><rect x="3" y="5" width="18" height="16" rx="2"/><path d="M3 10h18M8 3v4M16 3v4"/></svg><div><small>Date</small><span>22.04.2024</span></div></div>
    <div class="field"><svg width="20" height="20" viewBox="0 0 24 24" fill="none" stroke="#333" stroke-width="2"><circle cx="12" cy="8" r="4"/><path d="M4 21c0-4 4-6 8-6s8 2 8 6"/></svg><div><small>Participant</small><span>2 adults</span></div></div>
    <div class="explore">Explore</div>
  </div>

  <h2 class="abs section-title" style="left:118px;top:888px">Poppular Destination</h2>
  <div class="abs arrow-btn" style="left:970px;top:898px"><svg width="16" height="16" viewBox="0 0 24 24" fill="none" stroke="#222" stroke-width="2.5"><path d="M15 5l-7 7 7 7"/></svg></div>
  <div class="abs arrow-btn" style="left:1043px;top:898px"><svg width="16" height="16" viewBox="0 0 24 24" fill="none" stroke="#222" stroke-width="2.5"><path d="M9 5l7 7-7 7"/></svg></div>

  <div class="abs dest" style="left:118px"><div class="photo" role="img" aria-label="Eiffel Tower in Paris" style="background:linear-gradient(180deg,#4f8fd6,#8db6e0 60%,#5b7a3c)"></div><h3>Paris</h3><p>Voluptatibus Nemo Amet Voluptatem Quia Ipsa Eum. Est Ut Voluptas.</p><div class="meta"><span>◯ France</span><span>★ 4.92</span></div></div>
  <div class="abs dest" style="left:467px"><div class="photo" role="img" aria-label="Colosseum in Rome" style="background:linear-gradient(180deg,#3c7fd0,#8fb3dc 45%,#9a6a45)"></div><h3>Rome</h3><p>Voluptatibus Nemo Amet Voluptatem Quia Ipsa Eum. Est Ut Voluptas.</p><div class="meta"><span>◯ Italy</span><span>★ 4.92</span></div></div>
  <div class="abs dest" style="left:816px"><div class="photo" role="img" aria-label="Sydney Opera House at sunset" style="background:linear-gradient(180deg,#8a8fa3,#d39a6a 55%,#4d5a66)"></div><h3>Sydney</h3><p>Voluptatibus Nemo Amet Voluptatem Quia Ipsa Eum. Est Ut Voluptas.</p><div class="meta"><span>◯ Australia</span><span>★ 4.92</span></div></div>
  <div class="abs dest" style="left:1165px"><div class="photo" role="img" aria-label="Coastal destination" style="background:linear-gradient(180deg,#5aa3c7,#3d7f8a)"></div><h3>Rh</h3></div>

  <h2 class="abs section-title" style="left:116px;top:1544px">About Us</h2>
  <p class="abs lead" style="left:116px;top:1616px;width:760px">At Velorane, we redefine luxury air travel by offering a seamless and unparalleled experience for our discerning clients.</p>
  <div class="abs point" style="left:116px;top:1780px"><h4>1. Our mission</h4><p>To provide our clients with the ultimate freedom to travel wherever and whenever they desire.</p></div>
  <div class="abs point" style="left:397px;top:1780px"><h4>2. Exquisite Fleet</h4><p>Our fleet consists of top-of-the-line private jets, meticulously maintained to ensure safety and comfort on every journey.</p></div>
  <div class="abs point" style="left:116px;top:1982px"><h4>3. Global<br>&nbsp;&nbsp;&nbsp;&nbsp;Reach</h4><p>We make it possible for you to reach even the most remote destinations with ease and convenience.</p></div>
  <div class="abs point" style="left:411px;top:1982px"><h4>4. Personalized<br>&nbsp;&nbsp;&nbsp;&nbsp;Service</h4><p>Our dedicated team is committed to catering to your every need and preference.</p></div>
  <div class="abs engine" role="img" aria-label="Close-up of a private jet engine and wing"></div>

  <h2 class="abs section-title" style="left:116px;top:2524px;font-size:40px;line-height:62px">Why<br>Choose Us</h2>
  <div class="abs why-card" style="left:372px"><b>1.</b><h4>Unmatched Luxury</h4><p>Experience the height of luxury with our meticulously curated interiors, state-of-the-art amenities, and impeccable service.</p></div>
  <div class="abs why-card" style="left:622px"><b>2.</b><h4>Effortless Booking</h4><p>Booking platform allows you to effortlessly plan and customize your journey, ensuring a seamless experience from start to finish.</p></div>
  <div class="abs why-card" style="left:872px"><b>2.</b><h4>Peace of Mind</h4><p>Booking platform allows you to effortlessly plan and customize your journey, ensuring a seamless experience from start to finish.</p></div>

  <div class="abs loc-band"></div>
  <h2 class="abs section-title" style="left:0;width:1185px;text-align:center;top:2864px">Our Locations</h2>
  <div class="abs map" role="img" aria-label="City map showing Velorane location markers"></div>

  <div class="abs testi"></div>
  <h2 class="abs section-title" style="left:141px;top:3440px;line-height:62px">What They<br>Say</h2>
  <p class="abs" style="left:141px;top:3580px;width:330px;font-size:13px;line-height:26px;color:var(--dim)">Our Clients send us bunch of smilies with our services and we love them.</p>
  <div class="abs" style="left:141px;top:3652px;width:32px;height:32px;border-radius:50%;background:#fff;color:#999;text-align:center;line-height:32px">←</div>
  <div class="abs" style="left:201px;top:3652px;width:32px;height:32px;border-radius:50%;background:var(--blue);text-align:center;line-height:32px">→</div>
  <div class="abs back"><div style="position:absolute;left:28px;top:140px;font-size:15px">Marco Delvani</div><div style="position:absolute;left:28px;top:164px;font-size:11px">Rome, Italy</div></div>
  <div class="abs quote" style="left:601px;top:3467px;width:420px;height:202px">
    <p style="font-size:12px;line-height:26px">"On the Windows talking painted pasture yet its express parties use. Sure last upon he same as knew next. Of believed or diverted no."</p>
    <p style="margin-top:26px;font-size:14px">Adrian Kessel</p>
    <p style="font-size:11px;color:#999;margin-top:4px">Manchester, England</p>
  </div>
  <div class="abs avatar" role="img" aria-label="Client portrait"></div>

  <div class="abs contact"></div>
  <h2 class="abs section-title" style="left:113px;width:975px;text-align:center;top:3990px">Contact Us</h2>
  <div class="abs mail"><svg width="16" height="16" viewBox="0 0 24 24" fill="none" stroke="#aaa" stroke-width="2"><rect x="3" y="5" width="18" height="14" rx="2"/><path d="M3 7l9 6 9-6"/></svg>&nbsp;&nbsp;Enter your mail<span class="send">Send</span></div>

  <div class="abs brand" style="left:127px;top:4462px">Velorane<span class="brand-mark"></span></div>
  <p class="abs foot" style="left:127px;top:4512px;width:260px;font-size:13px;line-height:27px">Your Sky, Your Rules: Elevate Your Journey with Private Jet Rentals</p>
  <div class="abs social" style="left:129px;top:4582px"></div>
  <div class="abs social" style="left:184px;top:4582px;background:var(--blue)"></div>
  <div class="abs social" style="left:243px;top:4582px"></div>
  <div class="abs foot" style="left:603px;top:4472px"><h5>Pages</h5><ul><li>Home</li><li>About</li><li>Why Us</li><li>Location</li><li>Review</li><li>Contact</li></ul></div>
  <div class="abs foot" style="left:828px;top:4472px;width:260px">
    <h5>Contact</h5>
    <p style="margin-top:22px">☏&nbsp;&nbsp;01632 480257</p>
    <p style="margin-top:16px;text-decoration:underline">✉&nbsp;&nbsp;hello@velorane-air.co.uk</p>
    <p style="margin-top:16px;padding-left:28px;text-indent:-28px;line-height:18px">⌖&nbsp;&nbsp;&nbsp;Suite 9, Larkfield House, Brantwell Business Park, Orchard Lane Brantwell Ashcombe AB12 7QZ</p>
  </div>
  <p class="abs" style="left:127px;top:4712px;font-size:13px;color:var(--muted)">Copyright, Velorane 2024. All rights reserved.</p>
  <p class="abs" style="left:940px;top:4712px;font-size:13px;color:var(--muted)">Terms &amp; Conditions</p>
</div>
</body>
</html>
```